Logo + Label Design (Men’s Grooming Brand & Product Packaging)

Design a logo and 2 oz pomade label for Brel, a modern men’s grooming brand focused on clean, high-quality, natural ingredients. The design should establish a bold, masculine, minimalist identity that can later extend to products like shaving gel and body wash.

Key Requirements

Create a primary logo for “Brel” and a core label for the 2 oz pomade jar (screw-top).

Use a clean, modern style — masculine, confident, and approachable (think Dorran’s, Velta, Northfield Kit).

Design for 1–2 color screen printing on solid jar colors (white, black, or navy).

Avoid gradients, foil, or embossing. Must work in black & white.

Provide: vector logo, mockup of the 2 oz jar, color palette (CMYK/RGB/HEX), and font specs.

Winning design may lead to future projects (body wash, shave gel, skincare lines).

Font styles to use
Other font styles liked:
• We like the fonts and design concept in the attached mockup.

Requirements
Should not have
• We want to avoid too much writing or busy designs. We want to avoid having graphics/illustrations embedded in the logo if they will cause the brand to look less classy or sophisticated. We also want the design to look simple and all-American (e.g. Hollister and Vane, Pine Ledger, The KIM, etc). We’d like to give a Pellham & Royce vibe that feels classy and high end.

```html
<!DOCTYPE html>
<html lang="en">
<head>
<meta charset="utf-8">
<title>Brel Hair Pomade Label</title>
<link href="https://fonts.googleapis.com/css2?family=Archivo+Black&family=Ultra&family=Roboto:wght@300&display=swap" rel="stylesheet">
<style>
  :root {
    --page-bg: #ffffff;
    --label-cream: #fafaf5;
    --label-edge: #dcdcdc;
    --ink-black: #1a1a1a;
    --ink-grey: #6e6e70;
    --net-grey: #555558;
    --gold: #dba22a;
    --white: #ffffff;
  }
  * { margin: 0; padding: 0; box-sizing: border-box; }
  html, body {
    width: 1200px;
    height: 906px;
    overflow: hidden;
    background: var(--page-bg);
  }
  .canvas {
    position: relative;
    width: 1200px;
    height: 906px;
  }
  .label {
    position: absolute;
    left: 120px;
    top: 288px;
    width: 960px;
    height: 330px;
    background: var(--label-cream);
    border-top: 30px solid var(--label-edge);
    border-bottom: 24px solid var(--label-edge);
    border-radius: 10px;
  }
  .brand {
    position: absolute;
    left: 58px;
    top: 50px;
    display: flex;
    align-items: flex-start;
    gap: 10px;
  }
  .brand-name {
    font-family: "Ultra", serif;
    font-size: 150px;
    line-height: 1;
    color: var(--ink-black);
    letter-spacing: -4px;
  }
  .brand-dot {
    width: 22px;
    height: 22px;
    margin-top: 10px;
    border-radius: 50%;
    background: var(--gold);
  }
  .product {
    position: absolute;
    left: 390px;
    top: 44px;
    width: 520px;
    text-align: center;
  }
  .product-title {
    font-family: "Archivo Black", sans-serif;
    font-size: 64px;
    line-height: 1;
    color: var(--ink-black);
    letter-spacing: 1px;
  }
  .product-scent {
    margin-top: 10px;
    font-family: "Ultra", serif;
    font-size: 36px;
    line-height: 1;
    color: var(--ink-grey);
    letter-spacing: 3px;
  }
  .product-band {
    position: relative;
    margin: 14px auto 0;
    width: 510px;
    height: 48px;
  }
  .product-band svg {
    position: absolute;
    inset: 0;
  }
  .product-band-text {
    position: relative;
    display: flex;
    justify-content: center;
    align-items: center;
    gap: 14px;
    height: 48px;
    font-family: "Ultra", serif;
    font-size: 21px;
    color: var(--white);
    letter-spacing: 1px;
  }
  .band-diamond {
    width: 7px;
    height: 7px;
    background: var(--ink-black);
    transform: rotate(45deg);
  }
  .product-weight {
    margin-top: 14px;
    font-family: "Roboto", sans-serif;
    font-weight: 300;
    font-size: 25px;
    color: var(--net-grey);
  }
</style>
</head>
<body>
<main class="canvas">
  <section class="label">
    <div class="brand">
      <span class="brand-name">Brel</span>
      <span class="brand-dot"></span>
    </div>
    <div class="product">
      <h1 class="product-title">HAIR POMADE</h1>
      <p class="product-scent">FRESH &amp; CLEAN</p>
      <div class="product-band">
        <svg width="510" height="48" viewBox="0 0 510 48" aria-hidden="true">
          <polygon points="14,0 496,0 510,24 496,48 14,48 0,24" fill="var(--gold)"/>
        </svg>
        <div class="product-band-text">
          <span class="band-diamond"></span>
          <span>MEDIUM HOLD – MATTE FINISH</span>
          <span class="band-diamond"></span>
        </div>
      </div>
      <p class="product-weight">NET WT 2 OZ (57 G)</p>
    </div>
  </section>
</main>
</body>
</html>
```